New ecommerce website needed for Epoxy Retailer

We need a new shopify website designed and built for our epoxy supply store.
We sell Epoxy, wood, epoxy furniture, supplies and provide classes on how to use epoxy.
We are looking for a website with a home page and 7 primary navigation links at the top. Some of these links should have a drop down menu with the below listed pages linked to them...
Sub Pages:
- Nova Epoxy
- Epoxy
- Pigments
- Brindle Oil
- Molds
- Silicone
- HDPE
- Wood
- Live Edge
- Ovals & Rounds
- Pre-cut
- Charcuterie Wood
- Custom Milling
- Wholesale
- Supplies
- Furniture
-Education
- In person workshops
- My courses (are we able to have a login section for customers to see their purchases?)
- About Us

```html
<!DOCTYPE html>
<html lang="en">
<head>
<meta charset="utf-8">
<title>Timberpour Studio</title>
<link href="https://fonts.googleapis.com/css2?family=Source+Sans+3:wght@400;600;700&display=swap" rel="stylesheet">
<style>
:root{
  --ink:#111;
  --text:#333;
  --nav:#222;
  --muted:#666;
  --line:#e3e3e3;
  --tile:#f2f2f2;
  --badge:#c9c9c9;
  --frame:#bdbdbd;
  --field:#f0f0f0;
  --accent:#1f3f9a;
  --white:#fff;
}
*{margin:0;padding:0;box-sizing:border-box}
html,body{width:1200px;height:3243px;overflow:hidden;background:var(--white)}
body{position:relative;font-family:"Source Sans 3",sans-serif;color:var(--text)}
.abs{position:absolute}

/* header */
.site-header{left:0;top:0;width:1200px;height:103px;background:var(--white)}
.brand{left:112px;top:40px;display:flex;align-items:center;gap:8px;font-weight:700;font-size:20px;color:var(--ink);letter-spacing:.5px}
.brand-dot{width:14px;height:14px;border-radius:50%;background:var(--ink)}
.main-nav{left:306px;top:0;display:flex;height:103px;align-items:center}
.nav-link{font-size:15px;color:var(--nav);padding:0 10px;height:103px;line-height:103px;display:block}
.nav-link.active{background:#1b1b1b;color:var(--white);padding:0 12px}
.header-icons{left:1002px;top:45px;display:flex;gap:16px}

/* hero */
.hero{left:0;top:103px;width:1200px;height:586px;background:linear-gradient(135deg,#8a6a4c 0%,#5e4a3a 35%,#3f3530 55%,#7a5232 80%,#a3703e 100%)}
.hero-title{left:0;top:528px;width:1200px;text-align:center;font-size:51px;font-weight:700;color:var(--white)}
.hero-btn{left:540px;top:612px;width:121px;height:44px;border:2px solid var(--white);color:var(--white);font-weight:700;font-size:14px;display:flex;align-items:center;justify-content:center}
.slide-arrow{top:342px;width:58px;height:58px;border:2px solid var(--white);border-radius:50%}

/* products */
.section-title{left:0;top:766px;width:1200px;text-align:center;font-size:34px;font-weight:700;color:var(--ink);letter-spacing:.5px}
.product{width:233px}
.product-img{width:233px;height:194px;background:var(--tile);position:relative;overflow:hidden}
.product-art{position:absolute}
.sale{position:absolute;left:18px;bottom:14px;width:70px;height:24px;border-radius:12px;background:var(--badge);color:var(--white);font-size:13px;font-weight:700;text-align:center;line-height:24px;letter-spacing:.5px}
.product-name{margin-top:14px;font-size:16px;color:var(--muted)}
.product-price{margin-top:12px;font-size:19px;font-weight:700;color:var(--ink);padding-left:2px}

/* feature */
.feature-img{border-radius:3px}
.feature-label{font-size:20px;font-weight:700;color:var(--ink)}

/* video */
.video-frame{left:112px;top:2226px;width:976px;height:420px;background:var(--frame);box-shadow:0 24px 26px -18px rgba(0,0,0,.35)}
.video-still{left:13px;top:14px;width:950px;height:393px;background:linear-gradient(135deg,#8c6c4e,#4e4038 45%,#6f4a2c 75%,#9a6a3a)}
.play{left:447px;top:170px;width:82px;height:82px;border-radius:50%;background:var(--white)}

/* footer */
.foot-title{font-size:20px;font-weight:700;color:var(--ink)}
.quick-links{left:108px;top:2768px;list-style:none}
.quick-links li{font-size:12px;color:var(--text);height:31px;text-transform:uppercase}
.contact-item{left:468px;display:flex;gap:20px;font-size:12.5px;color:var(--text);line-height:21px}
.contact-item svg{flex:none;margin-top:4px}
.mission{left:828px;top:2762px;width:261px;font-size:12.5px;line-height:21.5px;text-align:justify;color:var(--text)}
.subscribe{left:112px;top:3033px;width:423px;height:44px;background:var(--field);display:flex;align-items:center;justify-content:space-between;padding:0 14px 0 18px;font-size:13px;color:var(--muted)}
.socials{left:909px;top:3008px;display:flex;gap:7px}
.socials span{width:30px;height:30px;border-radius:50%}
.divider{left:0;top:3108px;width:1200px;height:1px;background:var(--line)}
.copyright{left:0;top:3134px;width:1200px;text-align:center;font-size:13.5px;color:var(--ink)}
.cards{left:469px;top:3178px;display:flex;gap:8px}
.cards span{width:47px;height:21px;border:1px solid var(--line);border-radius:2px;background:var(--white)}
</style>
</head>
<body>

<header class="abs site-header">
  <div class="abs brand"><span class="brand-dot"></span>TIMBERPOUR</div>
  <nav class="abs main-nav">
    <span class="nav-link active">Home</span><span class="nav-link">Products</span><span class="nav-link">Wholesale</span><span class="nav-link">Supplies</span><span class="nav-link">Furniture</span><span class="nav-link">Education</span><span class="nav-link">My Courses</span><span class="nav-link">About Us</span>
  </nav>
  <div class="abs header-icons">
    <svg width="14" height="14" viewBox="0 0 14 14"><circle cx="6" cy="6" r="4.3" fill="none" stroke="#111" stroke-width="2"/><line x1="9" y1="9" x2="13" y2="13" stroke="#111" stroke-width="2"/></svg>
    <svg width="14" height="14" viewBox="0 0 14 14"><circle cx="7" cy="4.5" r="3.2" fill="none" stroke="#111" stroke-width="1.3"/><path d="M1.5 13.5c0-3.5 2.5-5 5.5-5s5.5 1.5 5.5 5z" fill="none" stroke="#111" stroke-width="1.3"/></svg>
    <svg width="16" height="14" viewBox="0 0 16 14"><path d="M5 5V3.5a3 3 0 0 1 6 0V5" fill="none" stroke="#111" stroke-width="1.5"/><rect x="1.5" y="5" width="13" height="9" fill="#111"/></svg>
  </div>
</header>

<section class="abs hero" role="img" aria-label="Craftsman pouring dark resin onto a live-edge wood slab in a workshop"></section>
<div class="abs slide-arrow" style="left:52px"><svg width="54" height="54" viewBox="0 0 54 54"><path d="M30 19l-8 8 8 8" fill="none" stroke="#fff" stroke-width="2.5"/></svg></div>
<div class="abs slide-arrow" style="left:1088px"><svg width="54" height="54" viewBox="0 0 54 54"><path d="M24 19l8 8-8 8" fill="none" stroke="#fff" stroke-width="2.5"/></svg></div>
<h1 class="abs hero-title">TIMBERPOUR STUDIO</h1>
<div class="abs hero-btn">SHOP NOW</div>

<h2 class="abs section-title">SHOP FOR OUR PRODUCTS</h2>

<div class="abs product" style="left:112px;top:843px"><div class="product-img"><div class="product-art" role="img" aria-label="Resin and wood coffee table" style="left:14px;top:40px;width:205px;height:140px;border-radius:6px;background:linear-gradient(180deg,#d99a52 0%,#b8763a 35%,#2a2a2a 55%,#1a1a1a 100%)"></div><span class="sale">SALE</span></div><p class="product-name">Nova Epoxy</p><p class="product-price">$799.00</p></div>
<div class="abs product" style="left:359px;top:843px"><div class="product-img"><div class="product-art" role="img" aria-label="Resin and wood pendant necklace" style="left:110px;top:70px;width:110px;height:60px;border-radius:30px;background:linear-gradient(90deg,#8a6a54 0%,#b99a80 40%,#2d5a9a 75%,#dfe6ee 100%)"></div></div><p class="product-name">Epoxy</p><p class="product-price">$799.00</p></div>
<div class="abs product" style="left:607px;top:843px"><div class="product-img"><div class="product-art" role="img" aria-label="River table with blue resin" style="left:32px;top:10px;width:170px;height:175px;border-radius:4px;background:linear-gradient(90deg,#c8904c 0%,#b07a40 38%,#1d4f7a 48%,#1d4f7a 54%,#b07a40 64%,#c8904c 100%)"></div><span class="sale">SALE</span></div><p class="product-name">Pigments</p><p class="product-price">$2380.00</p></div>
<div class="abs product" style="left:855px;top:843px"><div class="product-img"><div class="product-art" role="img" aria-label="Round wood slice set in turquoise resin" style="left:29px;top:10px;width:175px;height:175px;border-radius:50%;background:radial-gradient(circle,#c69a62 0%,#b88a52 50%,#3fd4b0 62%,#2ec9a3 100%)"></div><span class="sale">SALE</span></div><p class="product-name">Brindle Oil</p><p class="product-price">$1279.00</p></div>

<div class="abs product" style="left:112px;top:1169px"><div class="product-img"><div class="product-art" role="img" aria-label="Ocean-wave resin art on wood" style="left:30px;top:6px;width:185px;height:182px;border-radius:48% 52% 45% 55%;background:linear-gradient(150deg,#0f2a5a 0%,#2a4f8a 40%,#e6ecf2 58%,#1a1e2a 75%,#111 100%)"></div><span class="sale">SALE</span></div><p class="product-name">Molds</p><p class="product-price">$995.00</p></div>
<div class="abs product" style="left:359px;top:1169px"><div class="product-img"><div class="product-art" role="img" aria-label="Blue resin and wood pendant" style="left:20px;top:65px;width:200px;height:70px;border-radius:35px;background:linear-gradient(90deg,#0a3ed0 0%,#2a6ae0 35%,#7a5a3a 55%,#b8956c 80%,#dcd6cc 100%)"></div></div><p class="product-name">Silicone</p><p class="product-price">$1500.00</p></div>
<div class="abs product" style="left:607px;top:1169px"><div class="product-img"><div class="product-art" role="img" aria-label="Waterfall table with teal resin stripe" style="left:14px;top:20px;width:205px;height:150px;border-radius:4px;background:linear-gradient(160deg,#c98a42 0%,#2f9aa0 30%,#3aa8ad 40%,#d19048 55%,#2a2a2a 80%,#f2f2f2 100%)"></div><span class="sale">SALE</span></div><p class="product-name">HDPE</p><p class="product-price">$995.00</p></div>
<div class="abs product" style="left:855px;top:1169px"><div class="product-img"><div class="product-art" role="img" aria-label="Wood and green resin pendant on cord" style="left:150px;top:50px;width:60px;height:130px;border-radius:10px;background:linear-gradient(180deg,#9a6a40 0%,#6a4a2e 50%,#1fa58a 75%,#126b5c 100%)"></div><span class="sale">SALE</span></div><p class="product-name">Wood</p><p class="product-price">$995.00</p></div>

<div class="abs feature-img" style="left:112px;top:1559px;width:561px;height:510px;background:linear-gradient(160deg,#5d7a3a 0%,#7a8a4a 25%,#c4893e 50%,#2a4f9a 62%,#b57a3a 80%,#4b4a3a 100%)" role="img" aria-label="Wood and blue resin table outdoors on grass"></div>
<p class="abs feature-label" style="left:110px;top:2082px">NOVA EPOXY</p>
<div class="abs feature-img" style="left:701px;top:1559px;width:388px;height:207px;background:linear-gradient(180deg,#0e1422 0%,#2a2a2e 45%,#8a6a4a 55%,#1a1a1a 80%)" role="img" aria-label="Live-edge resin dining table on dark background"></div>
<p class="abs feature-label" style="left:701px;top:1781px">Epoxy</p>
<div class="abs feature-img" style="left:701px;top:1861px;width:388px;height:207px;background:linear-gradient(160deg,#4a4a52 0%,#6a6a70 40%,#8a5a36 55%,#3a2a22 70%,#5a5a60 100%)" role="img" aria-label="Dark resin and wood table in grey room"></div>
<p class="abs feature-label" style="left:701px;top:2082px">PIGMENTS</p>

<div class="abs video-frame">
  <div class="abs video-still" role="img" aria-label="Video still of resin being poured onto wood"></div>
  <div class="abs play"><svg width="82" height="82" viewBox="0 0 82 82"><path d="M33 28v26l21-13z" fill="#111"/></svg></div>
</div>

<h3 class="abs foot-title" style="left:108px;top:2715px">QUICK LINKS</h3>
<ul class="abs quick-links"><li>Home</li><li>About</li><li>Shop</li><li>Review</li><li>Science</li><li>Contact Us</li></ul>

<h3 class="abs foot-title" style="left:468px;top:2715px">GET IN TOUCH</h3>
<div class="abs contact-item" style="top:2765px"><svg width="14" height="11" viewBox="0 0 14 11"><rect width="14" height="11" fill="#111"/><path d="M0 0l7 6 7-6" fill="none" stroke="#fff" stroke-width="1"/></svg><div>Contact us at:<br>hello@timberpour.example</div></div>
<div class="abs contact-item" style="top:2829px"><svg width="14" height="14" viewBox="0 0 14 14"><path d="M3 1l3 3-1.5 1.5a8 8 0 0 0 4 4L10 8l3 3-2 2C6 13 1 8 1 3z" fill="#111"/></svg><div>Phone:<br>+1 888 888 8888</div></div>
<div class="abs contact-item" style="top:2893px"><svg width="14" height="14" viewBox="0 0 14 14"><path d="M7 1a4 4 0 0 1 4 4c0 3-4 8-4 8S3 8 3 5a4 4 0 0 1 4-4z" fill="#111"/><circle cx="7" cy="5" r="1.5" fill="#fff"/></svg><div>Address :<br>123,Lorem ipsum dolor sit amet,<br>consectetur</div></div>

<h3 class="abs foot-title" style="left:828px;top:2715px">OUR MISSION</h3>
<p class="abs mission">Lorem ipsum dolor sit amet, consectetur adipiscing elit, sed do eiusmod tempor incididunt ut labore et dolore magna aliqua.Lorem ipsum dolor sit amet, consectetur adipiscing elit, sed do eiusmod tempor incididunt ut labore et dolore magna aliqua.</p>

<h3 class="abs foot-title" style="left:112px;top:2980px">SUBSCRIBE TO OUR EMAILS</h3>
<div class="abs subscribe"><span>Email address</span><svg width="14" height="8" viewBox="0 0 14 8"><path d="M0 4h12M9 1l3 3-3 3" fill="none" stroke="var(--accent)" stroke-width="1.8"/></svg></div>

<div class="abs socials"><span style="background:#2f5aa8"></span><span style="background:#3b7be0"></span><span style="background:#3a8fd8"></span><span style="background:#c9387a"></span><span style="background:#c4182a"></span></div>

<div class="abs divider"></div>
<p class="abs copyright">© 2022 Timberpour Studio | All Rights Reserved</p>
<div class="abs cards"><span></span><span></span><span></span><span></span><span></span></div>

</body>
</html>
```